Marlowe Group needs a business card

I would like the card to be simple but modern and elegant.
I like black and white.
or black and gold.
we are a private finance lender and also are involved in property and property developments.

please look at the business card photos i provided i would like M.G only one one side and all the other details on the other side use fonts that tie in with my theme.

Industry/Entity Type

Finance

Contact Information for Business Card

Marlowe Group (M.G) Daniel Marlowe M: 0413586207 E: danmarl@inboxmail.test

Font styles to use
Other font styles liked:
• Use fonts that would reflect our business

Colors
000000
ffffff

Requirements
Must have
• one side of details
• other side has either M.G or Marlowe Group like in the photos provided

```html
<!DOCTYPE html>
<html lang="en">
<head>
<meta charset="utf-8">
<title>Marlowe Group — Business Card</title>
<link rel="stylesheet" href="https://fonts.googleapis.com/css2?family=Cinzel:wght@400&family=Source+Sans+3:wght@400;600&display=swap">
<style>
  :root {
    --backdrop: #b1b1b1;
    --card-black: #000000;
    --gold: #f7cf3c;
    --gold-bright: #ffd84a;
    --gold-light: #fee79d;
    --gold-deep: #efbf3a;
    --ink: #111111;
    --white: #ffffff;
  }
  * { margin: 0; padding: 0; box-sizing: border-box; }
  html, body {
    width: 1200px;
    height: 900px;
    overflow: hidden;
    background: var(--backdrop);
  }
  .canvas {
    position: relative;
    width: 1200px;
    height: 900px;
  }
  .card {
    position: absolute;
    top: 200px;
    height: 502px;
  }
  .card-front {
    left: 265px;
    width: 310px;
    background: var(--card-black);
    border-radius: 62px 0 62px 0;
  }
  .card-back {
    left: 641px;
    width: 308px;
    border-radius: 0 62px 0 62px;
    overflow: hidden;
  }
  .back-fill {
    position: absolute;
    inset: 0;
    background: linear-gradient(180deg, var(--gold-light) 0%, #f7d876 45%, var(--gold-deep) 100%);
  }
  .brand-mark {
    position: absolute;
    left: 147px;
    top: 110px;
    width: 16px;
    height: 16px;
    background: var(--gold);
  }
  .wordmark {
    position: absolute;
    left: 0;
    width: 100%;
    text-align: center;
    font-family: "Cinzel", serif;
    font-weight: 400;
    font-size: 24px;
    letter-spacing: 0.5px;
    white-space: nowrap;
  }
  .card-front .wordmark { top: 203px; color: var(--gold); }
  .card-back .wordmark { top: 413px; color: var(--ink); }
  .holder-name {
    position: absolute;
    left: 27px;
    top: 364px;
    font-family: "Source Sans 3", sans-serif;
    font-weight: 600;
    font-size: 18px;
    color: var(--gold-bright);
  }
  .contact-list {
    position: absolute;
    left: 29px;
    top: 417px;
    list-style: none;
    font-family: "Source Sans 3", sans-serif;
    font-size: 13.5px;
    color: var(--white);
  }
  .contact-item {
    display: flex;
    align-items: center;
    height: 21px;
  }
  .contact-icon {
    width: 10px;
    height: 10px;
    margin-right: 8px;
    fill: var(--gold);
  }
</style>
</head>
<body>
<main class="canvas">
  <section class="card card-front" aria-label="Card front">
    <div class="brand-mark" aria-hidden="true"></div>
    <p class="wordmark">Marlowe Group</p>
    <p class="holder-name">Daniel Marlowe</p>
    <ul class="contact-list">
      <li class="contact-item">
        <svg class="contact-icon" viewBox="0 0 10 10" aria-hidden="true"><path d="M2 0.5 L3.6 2.6 L2.7 3.7 C3.3 5 4.8 6.6 6.3 7.3 L7.4 6.4 L9.5 8 L8.4 9.5 C4.5 9.2 0.8 5.5 0.5 1.6 Z"/></svg>
        0413586207
      </li>
      <li class="contact-item">
        <svg class="contact-icon" viewBox="0 0 10 10" aria-hidden="true"><path d="M0.5 2 H9.5 V8.5 H0.5 Z M0.9 2.4 L5 5.6 L9.1 2.4" stroke="#000" stroke-width="0.7"/></svg>
        danmarl@inboxmail.test
      </li>
    </ul>
  </section>

  <section class="card card-back" aria-label="Card back">
    <div class="back-fill" role="img" aria-label="Soft gold gradient backdrop"></div>
    <p class="wordmark">Marlowe Group</p>
  </section>
</main>
</body>
</html>
```